Website for new crypto research organization

See brief (attached). This is a pretty basic website with only a handful of pages + ability to collect email addresses.

```html
<!DOCTYPE html>
<html lang="en">
<head>
<meta charset="utf-8">
<title>Tealstone Digital</title>
<link href="https://fonts.googleapis.com/css2?family=Montserrat:wght@500;600;700&family=Lato:wght@400;700&family=Poppins:wght@800&display=swap" rel="stylesheet">
<style>
:root{
  --teal:#189b9e;
  --blue:#1f98d1;
  --ink:#1c1c1c;
  --text:#2b2b2b;
  --muted:#555;
  --line:#9fd3d4;
  --card-border:#d6d6d6;
  --white:#fff;
  --band:#f7f9f9;
}
*{box-sizing:border-box;margin:0;padding:0}
html,body{width:1200px;height:3086px;overflow:hidden;background:var(--white)}
body{position:relative;font-family:'Lato',sans-serif;color:var(--text)}
.abs{position:absolute}
.heading{font-family:'Montserrat',sans-serif;color:var(--ink);font-weight:600}
.brand{font-family:'Montserrat',sans-serif;font-weight:700;color:var(--teal);display:flex;align-items:center;gap:8px}
.brand-square{width:18px;height:18px;background:var(--teal)}
.nav a{position:absolute;top:38px;font-family:'Montserrat',sans-serif;font-weight:500;font-size:15px;color:var(--ink);text-decoration:none}
.nav a.active{color:var(--blue);border-bottom:3px solid var(--blue);padding-bottom:4px}
.hero{left:0;top:97px;width:1200px;height:564px;background:linear-gradient(100deg,#8c8c8c 0%,#a09a95 30%,#7a5a3e 55%,#6d5440 65%,#8a8fa0 80%,#9a9c7f 100%)}
.hero-title{left:100px;top:318px;width:480px;font-family:'Poppins',sans-serif;font-weight:800;font-size:35px;line-height:39px;color:var(--white)}
.btn{display:flex;align-items:center;justify-content:center;font-family:'Montserrat',sans-serif;font-weight:700;text-transform:uppercase;text-decoration:none}
.btn-solid{background:var(--teal);color:var(--white)}
.btn-outline{border:2px solid var(--teal);color:var(--teal);background:var(--white)}
.hero-btn{left:104px;top:495px;width:121px;height:41px;font-size:13px;border:2px solid var(--white)}
.about-block h2{font-size:26px}
.about-block h3{font-size:20px}
.copy{font-size:14px;line-height:20px;color:var(--text)}
.link-more{font-family:'Montserrat',sans-serif;font-weight:700;font-size:13px;color:var(--teal);display:flex;align-items:center;gap:10px}
.about-art{left:663px;top:728px;width:396px;height:396px;border-radius:50%;background:radial-gradient(circle at 50% 45%,#e6c24a 0%,#d9a94a 25%,#c9a7a0 50%,#a6b4b8 75%,#9b9b9b 100%)}
.research-card{top:1354px;height:462px;border-top:1px solid var(--line);border-bottom:1px solid var(--line)}
.research-card .date{position:absolute;top:32px;font-size:14px}
.research-card .title{position:absolute;top:62px;width:265px;font-family:'Montserrat',sans-serif;font-weight:600;font-size:18px;line-height:24px;color:var(--ink)}
.research-card .copy{position:absolute;top:152px;width:240px;font-size:14px;line-height:20px}
.research-card .btn{position:absolute;top:369px;width:102px;height:34px;font-size:11px}
.card-featured{background:var(--teal);color:var(--white)}
.card-featured .title{color:var(--white)}
.card-featured .btn{background:var(--white);color:var(--teal)}
.news-card{top:1956px;width:298px;height:374px;border:1px solid var(--card-border);box-shadow:0 1px 3px rgba(0,0,0,.06)}
.news-card .tag{position:absolute;left:26px;top:31px;height:26px;padding:0 10px;border:1px solid #444;font-size:12px;line-height:24px}
.news-card .date{position:absolute;left:26px;top:76px;font-size:13px}
.news-card .title{position:absolute;left:26px;top:98px;width:250px;font-family:'Montserrat',sans-serif;font-weight:600;font-size:15px;line-height:20px;color:var(--ink)}
.news-card .copy{position:absolute;left:26px;top:179px;width:250px;font-size:13px;line-height:17.5px;color:var(--muted)}
.news-card .btn{position:absolute;left:27px;top:304px;width:102px;height:34px;font-size:11px}
.newsletter-band{left:0;top:2393px;width:1200px;height:411px;background:var(--band);border-top:1px solid var(--line);border-bottom:1px solid var(--line)}
.newsletter-box{left:374px;top:2453px;width:457px;height:290px;background:var(--white);border:6px solid var(--teal);text-align:center}
.field{left:428px;top:2638px;width:230px;height:49px;border:1px solid #999;font-size:13px;color:#444;padding:0 15px;display:flex;align-items:center;background:var(--white)}
.subscribe{left:658px;top:2638px;width:128px;height:49px;background:var(--blue);color:var(--white);font-family:'Montserrat',sans-serif;font-weight:700;font-size:17px;display:flex;align-items:center;justify-content:center}
.footer-links a{display:block;font-family:'Montserrat',sans-serif;font-size:12px;line-height:19.2px;color:var(--ink);text-decoration:none}
.social{width:32px;height:32px;border-radius:50%}
</style>
</head>
<body>

<header>
  <div class="abs brand" style="left:132px;top:34px;font-size:20px"><span class="brand-square"></span>Tealstone Digital</div>
  <nav class="nav">
    <a href="#" class="active" style="left:471px">HOME</a>
    <a href="#" style="left:563px">ABOUT</a>
    <a href="#" style="left:660px">RESEARCH</a>
    <a href="#" style="left:790px">NEWS</a>
    <a href="#" style="left:880px">CAREERS</a>
    <a href="#" style="left:994px">CONTACT</a>
  </nav>
</header>

<section>
  <div class="abs hero" role="img" aria-label="Elephant breaking through a graffiti-painted brick wall with a red heart"></div>
  <h1 class="abs hero-title">A thematic, research-driven digital asset investment firm built for founders.</h1>
  <a href="#" class="abs btn btn-solid hero-btn">Read More</a>
</section>

<section class="about-block">
  <h2 class="abs heading" style="left:133px;top:714px">About us</h2>
  <p class="abs copy" style="left:133px;top:763px;width:450px">There are many variations of passages of Lorem Ipsum available, but the majority have suffered alteration in some form, by injected humour, or randomised words which don't look even slightly believable.</p>
  <a href="#" class="abs link-more" style="left:133px;top:844px">READ MORE
    <svg width="40" height="14" viewBox="0 0 40 14"><path d="M0 7H38M31 1L38 7L31 13" fill="none" stroke="#189b9e" stroke-width="2"/></svg></a>
  <h3 class="abs heading" style="left:133px;top:898px">Who we are</h3>
  <p class="abs copy" style="left:133px;top:931px;width:450px">There are many variations of passages of Lorem Ipsum available, but the majority have suffered alteration in some form.</p>
  <h3 class="abs heading" style="left:133px;top:1009px">Vision</h3>
  <p class="abs copy" style="left:133px;top:1042px;width:450px">There are many variations of passages of Lorem Ipsum available, but the majority have suffered alteration in some form.</p>
  <h3 class="abs heading" style="left:133px;top:1115px">Mission</h3>
  <p class="abs copy" style="left:133px;top:1148px;width:450px">There are many variations of passages of Lorem Ipsum available, but the majority have suffered alteration in some form.</p>
  <div class="abs about-art" role="img" aria-label="Colourful abstract geometric sculpture in a concrete room"></div>
</section>

<section>
  <h2 class="abs heading" style="left:130px;top:1283px;font-size:26px">Research</h2>
  <a href="#" class="abs btn btn-outline" style="left:308px;top:1280px;width:221px;height:40px;font-size:12px;text-transform:none;font-weight:600">Most Recent Research Reports</a>

  <article class="abs research-card card-featured" style="left:0;width:425px">
    <div class="date" style="left:132px">09.2.2022</div>
    <h3 class="title" style="left:132px">Lorem Ipsum is simply dum my text of the printing</h3>
    <p class="copy" style="left:132px">There are many variations of passages of Lorem Ipsum available, but the majority have suffered alteration in some form, by injected humour, or randomised words which don't look even slightly believable. If you are going to use a passage of Lorem Ipsum, you need to be sure .</p>
    <a href="#" class="btn" style="left:131px">Read More</a>
  </article>
  <article class="abs research-card" style="left:425px;width:388px;border-right:1px solid var(--line)">
    <div class="date" style="left:39px">09.2.2022</div>
    <h3 class="title" style="left:39px">Lorem Ipsum is simply dum my text of the printing</h3>
    <a href="#" class="btn btn-solid" style="left:38px">Read More</a>
  </article>
  <article class="abs research-card" style="left:813px;width:387px">
    <div class="date" style="left:35px">09.2.2022</div>
    <h3 class="title" style="left:35px">Lorem Ipsum is simply dum my text of the printing</h3>
    <a href="#" class="btn btn-solid" style="left:34px">Read More</a>
  </article>
</section>

<section>
  <h2 class="abs heading" style="left:129px;top:1884px;font-size:26px">Latest News</h2>
  <a href="#" class="abs btn btn-outline" style="left:329px;top:1882px;width:120px;height:41px;font-size:12px">Read More</a>

  <article class="abs news-card" style="left:130px">
    <span class="tag">Articles</span><div class="date">11.2.2022</div>
    <h3 class="title">Lorem Ipsum is simply dum my text of the printing but also the leap into electronic.</h3>
    <p class="copy">Sed ut perspiciatis unde omnis iste natus error sit voluptatem accusantium doloremque laudantium, totam rem aperiam, eaque ipsa quae ab illo inventore veritatis et quasi architecto beatae vitae</p>
    <a href="#" class="btn btn-solid">Read More</a>
  </article>
  <article class="abs news-card" style="left:449px">
    <span class="tag">Articles</span><div class="date">11.2.2022</div>
    <h3 class="title">Lorem Ipsum is simply dum my text of the printing but also the leap into electronic.</h3>
    <p class="copy">Sed ut perspiciatis unde omnis iste natus error sit voluptatem accusantium doloremque laudantium, totam rem aperiam, eaque ipsa quae ab illo inventore veritatis et quasi architecto beatae vitae</p>
    <a href="#" class="btn btn-solid">Read More</a>
  </article>
  <article class="abs news-card" style="left:767px">
    <span class="tag">Articles</span><div class="date">11.2.2022</div>
    <h3 class="title">At vero eos et accusamus et iusto odio dignissimos ducimus qui blanditiis praesentium</h3>
    <p class="copy">Sed ut perspiciatis unde omnis iste natus error sit voluptatem accusantium doloremque laudantium, totam rem aperiam, eaque ipsa quae ab illo inventore veritatis et quasi architecto beatae vitae</p>
    <a href="#" class="btn btn-solid">Read More</a>
  </article>
</section>

<section>
  <div class="abs newsletter-band" role="img" aria-label="Light diagonal line pattern background"></div>
  <div class="abs newsletter-box">
    <div class="brand" style="justify-content:center;margin-top:42px;font-size:20px">Tealstone Digital</div>
    <h2 class="heading" style="font-size:24px;font-weight:500;margin-top:26px">Newsletter Subscribe</h2>
    <p style="font-size:16px;margin-top:8px">Get more details to signup</p>
  </div>
  <div class="abs field">Type your email...</div>
  <div class="abs subscribe">Subscribe</div>
</section>

<footer>
  <div class="abs brand" style="left:132px;top:2878px;font-size:22px"><span class="brand-square"></span>Tealstone Digital</div>
  <nav class="abs footer-links" style="left:819px;top:2838px">
    <a href="#">HOME</a><a href="#">ABOUT</a><a href="#">RESEARCH</a><a href="#">NEWS</a><a href="#">CAREERS</a><a href="#">CONTACT</a>
  </nav>
  <div class="abs" style="left:997px;top:2838px;font-family:'Montserrat',sans-serif;font-size:12px;color:var(--ink)">FOLLOW US</div>
  <div class="abs social" style="left:997px;top:2870px;background:var(--blue)"></div>
  <div class="abs social" style="left:1037px;top:2870px;background:#1a4f6b"></div>
  <div class="abs" style="left:0;top:2990px;width:1200px;border-top:1px solid var(--line)"></div>
  <p class="abs" style="left:0;top:3030px;width:1200px;text-align:center;font-family:'Montserrat',sans-serif;font-size:13px;color:var(--ink)">Copyright © 2022 All Rights Reserved</p>
</footer>

</body>
</html>
```